I will ask the design of the business card

We are looking for business card design of the new company "R DOVE PAYGRID WORKS LLC." Based in Azerbaijan.
In case
We are working on Azerbaijan to set up the first exchange of crypto currencies.

The key currency used in exchanges is called "PLUME".
In case
We are doing project to make crypto currency infrastructure.

We provide state-of-the-art technology to the world.

```html
<!DOCTYPE html>
<html lang="en">
<head>
<meta charset="utf-8">
<title>R Dove Paygrid Works LLC. — Business Card</title>
<link rel="stylesheet" href="https://fonts.googleapis.com/css2?family=Open+Sans:wght@700&family=Arimo:wght@400;700&family=Bebas+Neue&display=swap">
<style>
  :root {
    --page-bg: #8a5a34;
    --kraft-light: #dcb98d;
    --kraft-mid: #c99d6c;
    --kraft-dark: #b6875a;
    --ink: #111111;
  }
  * { margin: 0; padding: 0; box-sizing: border-box; }
  html, body { width: 1200px; height: 900px; overflow: hidden; }
  body {
    background: var(--page-bg);
    position: relative;
    color: var(--ink);
    font-family: "Arimo", Arial, sans-serif;
  }
  .card {
    position: absolute;
    width: 556px;
    height: 343px;
    background: radial-gradient(ellipse at 30% 0%, var(--kraft-light) 0%, var(--kraft-mid) 55%, var(--kraft-dark) 100%);
  }
  .card--front { left: 330px; top: 90px; }
  .card--back { left: 330px; top: 469px; width: 558px; }

  .contact {
    position: absolute;
    left: 0; right: 0; top: 62px;
    text-align: center;
    padding-left: 53px;
  }
  .contact__name {
    font-family: "Open Sans", Arial, sans-serif;
    font-weight: 700;
    font-size: 20px;
    line-height: 26px;
    letter-spacing: 0.3px;
  }
  .contact__role {
    font-size: 16px;
    line-height: 20px;
  }
  .contact__rule {
    width: 195px;
    height: 1px;
    background: var(--ink);
    margin: 11px auto 12px;
  }
  .contact__lines {
    list-style: none;
    font-size: 16px;
    line-height: 20.3px;
  }
  .contact__label { font-weight: 700; }
  .contact__address {
    font-size: 16px;
    line-height: 20px;
    font-style: normal;
    margin-top: 18px;
  }

  .company {
    position: absolute;
    left: 0; right: 0; top: 146px;
    text-align: center;
    font-family: "Bebas Neue", Impact, sans-serif;
    font-size: 47px;
    line-height: 50px;
    letter-spacing: 0.3px;
  }
</style>
</head>
<body>
  <section class="card card--front" aria-label="Card front">
    <div class="contact">
      <h1 class="contact__name">DANIEL HARROW</h1>
      <p class="contact__role">Managing Director</p>
      <div class="contact__rule"></div>
      <ul class="contact__lines">
        <li><span class="contact__label">P:</span> 044-987 654 321</li>
        <li><span class="contact__label">M:</span> 044-987 654 321</li>
        <li><span class="contact__label">E:</span> hello@dovepaygrid.com</li>
        <li><span class="contact__label">W:</span> www.dovepaygrid.com</li>
      </ul>
      <div class="contact__rule"></div>
      <address class="contact__address">12345, Address Goes Here<br>Country Name, 123456.</address>
    </div>
  </section>

  <section class="card card--back" aria-label="Card back">
    <h2 class="company">R DOVE PAYGRID WORKS LLC.</h2>
  </section>
</body>
</html>
```